Business card por a urban DJ, up scale audience target

Need a sober design, modern, conservative colors but i can consider some options, y play rnb, hip hop, EDM and top40.

Business card for contact and personal info, double sided, use logo attrached please; im 42 so i need a card acording to my age an target audience.

Target Market(s)

Adult people, up scale audience

Industry/Entity Type

Music Download

Contact Information for Business Card

Cel (318) 4207265518 www.lumadrift.com

Requirements
Must have
• open mind
Nice to have
• open mind
Should not have
• DJ

```html
<!DOCTYPE html>
<html lang="en">
<head>
<meta charset="utf-8">
<title>Luma Drift – Business Card</title>
<link rel="stylesheet" href="https://fonts.googleapis.com/css2?family=Open+Sans:wght@400;700&display=swap">
<style>
  :root {
    --page: #e9e7e3;
    --card-white: #ffffff;
    --card-black: #1b1b1b;
    --ink: #1c1c1c;
    --band-mid-top: #8c8c8c;
    --band-mid-bottom: #b9b9b9;
    --band-line: #6e6e6e;
    --band-dark: #262626;
    --text-light: #f2f2f2;
    --text-soft: #d6d6d6;
    --text-muted: #4a4a4a;
  }
  * { box-sizing: border-box; margin: 0; padding: 0; }
  html, body {
    width: 1200px; height: 950px; overflow: hidden;
    background: var(--page);
    font-family: "Open Sans", Arial, sans-serif;
  }
  .sheet {
    width: 1200px; height: 950px;
    display: flex; flex-direction: column;
    align-items: center; justify-content: center; gap: 40px;
  }
  .card {
    width: 740px; height: 423px;
    border-radius: 4px;
    overflow: hidden;
    box-shadow: 0 10px 28px rgba(0,0,0,.22);
    position: relative;
  }

  /* Front */
  .card--front { background: var(--card-white); display: flex; flex-direction: column; }
  .front__brand {
    flex: 0 0 56%;
    display: flex; align-items: center; justify-content: center;
  }
  .brand-name {
    font-weight: 700; color: var(--ink);
    font-size: 92px; letter-spacing: 6px; line-height: 1;
  }
  .front__identity {
    flex: 0 0 20%;
    background: linear-gradient(180deg, var(--band-mid-top), var(--band-mid-bottom));
    border-bottom: 6px solid var(--band-line);
    display: flex; align-items: center; justify-content: center; gap: 18px;
    color: var(--text-light); font-size: 26px;
  }
  .identity__name { font-weight: 700; }
  .identity__sep { font-weight: 700; }
  .identity__role { font-weight: 400; color: var(--text-muted); }
  .front__contact {
    flex: 1;
    background: var(--band-dark);
    display: flex; align-items: center; justify-content: center; gap: 16px;
    color: var(--text-soft); font-size: 26px; letter-spacing: .5px;
  }
  .contact__divider { color: var(--text-soft); }

  /* Back */
  .card--back {
    background: linear-gradient(135deg, #222 0%, var(--card-black) 55%, #101010 100%);
    display: flex; flex-direction: column; align-items: center; justify-content: center; gap: 26px;
  }
  .card--back .brand-name { color: var(--text-light); font-size: 120px; letter-spacing: 8px; }
  .back__url {
    color: var(--text-soft); font-size: 22px; letter-spacing: 4px;
  }
</style>
</head>
<body>
  <main class="sheet">
    <section class="card card--front" aria-label="Business card front">
      <div class="front__brand">
        <span class="brand-name">LUMA</span>
      </div>
      <div class="front__identity">
        <span class="identity__name">Marco Hale</span>
        <span class="identity__sep">-</span>
        <span class="identity__role">President</span>
      </div>
      <div class="front__contact">
        <span class="contact__phone">(318) 4207265518</span>
        <span class="contact__divider">|</span>
        <span class="contact__web">www.lumadrift.com</span>
      </div>
    </section>

    <section class="card card--back" aria-label="Business card back">
      <span class="brand-name">LUMA</span>
      <span class="back__url">LUMADRIFT.COM</span>
    </section>
  </main>
</body>
</html>
```